Modern Business Card for Larkwell 2018

Our company assumes the best about people. We are creating an online community of entrepreneurs and business leaders who struggle with marketing their business online.

This business card should POP! We recently got a new logo and are launching a new website next month, so our business cards should make a statement that feels:
-Fresh
-Smart
-Trustworthy
-Fun

Target Market(s)

small business owners, entrepreneurs

Industry/Entity Type

Digital Marketing

Contact Information for Business Card

Dimensions: 3.5" x 2"

Font styles to use
Sans Serif

Colors
f37122
ffffff

Requirements
Must have
• We need a business card with a modern, bold design. We will use one side of the card as a lead-generation offer, so text on one side will need to fit up to 140 characters. The business card should stick to our core colors (orange, black, and white).
Nice to have
• We think a vertical "portrait" design could be interesting.
Should not have
• Should not look like a traditional business card. The round icon should stand out from a distance.

```html
<!DOCTYPE html>
<html lang="en">
<head>
<meta charset="utf-8">
<title>Larkwell Business Card</title>
<link rel="stylesheet" href="https://fonts.googleapis.com/css2?family=Open+Sans:wght@400;600;700;800&display=swap">
<style>
  :root {
    --orange: #f37122;
    --white: #ffffff;
    --ink: #2b2b2b;
    --grey: #6b6b6b;
    --line: #4a4a4a;
    --stage: #e9e7e4;
  }
  * { box-sizing: border-box; margin: 0; padding: 0; }
  html, body {
    width: 1200px; height: 950px; overflow: hidden;
    background: var(--stage);
    font-family: "Open Sans", Arial, sans-serif;
  }
  .canvas {
    position: relative; width: 1200px; height: 950px;
    display: flex; align-items: center; justify-content: center; gap: 40px;
  }
  .card {
    position: relative; width: 540px; height: 309px;
    border-radius: 4px;
    box-shadow: 0 6px 18px rgba(0,0,0,.18);
    overflow: hidden;
  }

  /* Front */
  .card-front { background: var(--white); }
  .brand {
    position: absolute; left: 44px; bottom: 48px;
  }
  .brand-mark {
    display: block; width: 34px; height: 34px; border-radius: 50%;
    background: var(--orange); margin-bottom: 10px;
  }
  .brand-name {
    font-weight: 800; font-size: 46px; letter-spacing: 1px; line-height: 1;
    color: var(--ink);
  }
  .brand-tagline {
    margin-top: 6px; font-weight: 600; font-size: 11.5px;
    letter-spacing: 1.6px; text-transform: uppercase; color: var(--ink);
  }
  .contact {
    position: absolute; right: 40px; top: 44px; text-align: right;
  }
  .contact-name {
    font-weight: 700; font-size: 20px; color: var(--orange);
    text-transform: uppercase; letter-spacing: .3px;
  }
  .contact-role {
    margin-top: 4px; font-weight: 700; font-size: 14px; color: var(--ink);
    text-transform: uppercase; letter-spacing: .3px;
  }
  .contact-email {
    margin-top: 4px; font-size: 14px; color: var(--grey);
  }

  /* Back */
  .card-back { background: var(--orange); }
  .back-mark {
    position: absolute; left: 36px; top: 34px;
    width: 120px; height: 120px; border-radius: 50%;
    background: var(--white);
  }
  .back-divider {
    position: absolute; left: 186px; top: 30px; width: 1px; height: 130px;
    background: rgba(255,255,255,.55);
  }
  .offer {
    position: absolute; left: 210px; top: 30px; right: 30px; color: var(--white);
  }
  .offer-headline {
    font-weight: 800; font-size: 20px; line-height: 1.1;
    text-transform: uppercase; letter-spacing: .2px;
  }
  .offer-body {
    margin-top: 8px; font-size: 12.5px; line-height: 1.35;
  }
  .offer-url {
    margin-top: 6px; font-weight: 700; font-size: 15px;
  }
  .notes {
    position: absolute; left: 30px; right: 30px; bottom: 26px; height: 96px;
    background: var(--white); border-radius: 0 12px 12px 0;
    padding: 0 20px;
    display: flex; flex-direction: column; justify-content: space-evenly;
  }
  .notes-line { height: 1px; background: var(--line); }
</style>
</head>
<body>
<main class="canvas">
  <section class="card card-front" aria-label="Card front">
    <div class="brand">
      <span class="brand-mark"></span>
      <div class="brand-name">LARKWELL</div>
      <div class="brand-tagline">Share ideas that move people</div>
    </div>
    <div class="contact">
      <div class="contact-name">Dana Whitlow</div>
      <div class="contact-role">Story Marketing Coach</div>
      <div class="contact-email">dana@larkwellnow.com</div>
    </div>
  </section>

  <section class="card card-back" aria-label="Card back">
    <span class="back-mark"></span>
    <span class="back-divider"></span>
    <div class="offer">
      <div class="offer-headline">Reach more people.<br>Make more money.<br>Create more impact.</div>
      <p class="offer-body">Get your free Larkwell Starter Package and our marketing guide today at</p>
      <div class="offer-url">Larkwellnow.com/start</div>
    </div>
    <div class="notes">
      <span class="notes-line"></span>
      <span class="notes-line"></span>
    </div>
  </section>
</main>
</body>
</html>
```